Rebrand stationary with recently completed logo design

Need new business cards, thank you cards, letterhead, envelopes and presentation folders. The designs will be sent to a separate production firm so I need the files to be print ready.

My contact info
Reko Haliburn

Office 604-318-5047
Fax 604-371-8054

Email reko@glazemark.ca
website www.glazemark.ca

315-14720 62nd Avenue,
Langley, BC, V2K 3R8

Target Market(s)

Homeowners, businesses and contractors

Industry/Entity Type

Business

Font styles to use
Sans Serif

Colors
34a7d7

Requirements
Must have
• Like to have one side of the business card a solid color with the logo in all white. The side with all the text to be a white background
• I find the current blue on the front of the card with the white logo too dark.
Should not have
• Gradient colors

```html
<!DOCTYPE html>
<html lang="en">
<head>
<meta charset="utf-8">
<title>Glazemark Business Card</title>
<link href="https://fonts.googleapis.com/css2?family=Open+Sans:wght@400;600&family=Open+Sans+Condensed:wght@700&display=swap" rel="stylesheet">
<style>
  :root {
    --stage: #232425;
    --card-white: #f3f3f3;
    --brand-blue: #1590d4;
    --brand-slate: #46505a;
    --text-grey: #4b4f54;
    --rule-grey: #8a8e93;
    --white: #ffffff;
  }
  * { margin: 0; padding: 0; box-sizing: border-box; }
  html, body {
    width: 1200px; height: 960px; overflow: hidden;
    background: var(--stage);
    font-family: "Open Sans", Arial, sans-serif;
  }
  .canvas { position: relative; width: 1200px; height: 960px; }

  .card { position: absolute; width: 600px; height: 342px; overflow: hidden; }
  .card-front { left: 302px; top: 129px; background: var(--card-white); }
  .card-back { left: 299px; top: 488px; background: var(--brand-blue); }

  .brand-name {
    position: absolute; font-weight: 400; letter-spacing: 0.5px;
    line-height: 1; white-space: nowrap;
  }
  .card-front .brand-name { right: 34px; top: 60px; font-size: 38px; color: var(--brand-slate); }
  .card-back .brand-name { left: 0; right: 0; top: 204px; text-align: center; font-size: 46px; color: var(--white); }

  .holder-name {
    position: absolute; left: 29px; top: 204px;
    font-family: "Open Sans Condensed", "Arial Narrow", sans-serif;
    font-weight: 700; font-size: 21px; color: var(--brand-blue); letter-spacing: 0.3px;
  }
  .holder-rule {
    position: absolute; left: 29px; top: 236px; width: 536px; height: 1px;
    background: var(--rule-grey);
  }
  .contact-list { position: absolute; left: 29px; top: 247px; list-style: none; }
  .contact-list li {
    display: flex; align-items: center; height: 19.5px;
    font-size: 13px; color: var(--text-grey);
  }
  .contact-list svg { width: 13px; height: 13px; margin-right: 9px; fill: var(--brand-blue); }

  .address {
    position: absolute; right: 35px; top: 262px; text-align: right;
    font-size: 13px; line-height: 18px; color: var(--text-grey); font-style: normal;
  }

  .footer-band { position: absolute; left: 0; bottom: 0; width: 600px; height: 26px; }
  .web-address {
    position: absolute; right: 14px; bottom: 5px;
    font-size: 13px; font-weight: 600; color: var(--white); letter-spacing: 4.4px;
  }
</style>
</head>
<body>
<main class="canvas">

  <section class="card card-front">
    <div class="brand-name">GLAZEMARK</div>

    <h1 class="holder-name">REKO HALIBURN</h1>
    <div class="holder-rule"></div>

    <ul class="contact-list">
      <li>
        <svg viewBox="0 0 16 16" aria-hidden="true"><path d="M3.6 1.2l2.3 2.6c.4.4.3 1-.1 1.4L4.6 6.3c.9 2 2.6 3.8 4.9 5l1.1-1.2c.4-.4 1-.5 1.4-.1l2.6 2.2c.4.4.5 1 .1 1.4l-1.3 1.4c-.6.6-1.5.8-2.3.5C6 13.9 2.3 10.1.7 5 .4 4.2.6 3.3 1.2 2.7l1.1-1.4c.3-.4 1-.5 1.3-.1z"/></svg>
        604-318-5047
      </li>
      <li>
        <svg viewBox="0 0 16 16" aria-hidden="true"><path d="M4 1h8v4H4z M1 6h14v6h-2v-2H3v2H1z M4 11h8v4H4z"/></svg>
        604-371-8054
      </li>
      <li>
        <svg viewBox="0 0 16 16" aria-hidden="true"><path d="M1 3h14v10H1z"/><path d="M1.5 3.5L8 9l6.5-5.5" fill="none" stroke="#fff" stroke-width="1.3"/></svg>
        reko@glazemark.ca
      </li>
    </ul>

    <address class="address">
      315-14720 62nd Avenue<br>
      Langley, BC, V2K 3R8
    </address>

    <svg class="footer-band" viewBox="0 0 600 26" aria-hidden="true">
      <rect x="0" y="12" width="362" height="14" fill="var(--brand-slate)"/>
      <polygon points="346,26 370,2 600,2 600,26" fill="var(--white)"/>
      <polygon points="352,26 374,5 600,5 600,26" fill="var(--brand-blue)"/>
    </svg>
    <div class="web-address">www.glazemark.ca</div>
  </section>

  <section class="card card-back">
    <div class="brand-name">GLAZEMARK</div>
  </section>

</main>
</body>
</html>
```